Business Card Design for Occupational Medicine Start Up Company

We need to design a professional business card. We are a healthcare company providing occupational medicine services to blue collar industries. We are professional, efficient and high quality service providers.

Target Market(s)

Blue Collar Industry: Shipbuilding, Ports, Trucking Companies; The Executives and Safety Officers for these companies

Industry/Entity Type

Healthcare

Contact Information for Business Card

Logo, Name, Title, Email, Phone

Other font styles liked:
• Please match our Brand Guide

Requirements
Must have
• Our Company Colors and Logo

```html
<!DOCTYPE html>
<html lang="en">
<head>
<meta charset="utf-8">
<title>CrewCare Clinics Business Card</title>
<link href="https://fonts.googleapis.com/css2?family=Montserrat:ital,wght@0,400;0,500;0,700;0,800;1,400&display=swap" rel="stylesheet">
<style>
  :root {
    --navy: #2e3480;
    --orange: #f5a623;
    --sky: #1e9ad6;
    --paper: #ffffff;
    --ink-soft: #4a4a55;
    --stage: #e9eaee;
  }
  * { margin: 0; padding: 0; box-sizing: border-box; }
  html, body {
    width: 1200px; height: 900px; overflow: hidden;
    background: var(--stage);
    font-family: "Montserrat", Arial, sans-serif;
  }
  .sheet {
    width: 1200px; height: 900px;
    display: flex; flex-direction: column; align-items: center; justify-content: center;
    gap: 40px;
  }
  .card {
    position: relative;
    width: 700px; height: 400px;
    box-shadow: 0 6px 18px rgba(0,0,0,0.12);
  }
  .card-front { background: var(--paper); }
  .card-back {
    background: var(--navy);
    display: flex; align-items: center; justify-content: center;
  }
  .brand {
    display: flex; align-items: center; gap: 14px;
    font-weight: 800; letter-spacing: 0.04em; text-transform: uppercase;
  }
  .brand-dot { width: 18px; height: 18px; border-radius: 50%; }
  .card-front .brand {
    position: absolute; left: 56px; top: 64px;
    color: var(--navy); font-size: 30px;
  }
  .card-front .brand-dot { background: var(--orange); }
  .card-back .brand { color: var(--paper); font-size: 44px; }
  .card-back .brand-dot { background: var(--orange); width: 24px; height: 24px; }
  .divider {
    position: absolute; left: 56px; right: 56px; top: 200px;
    height: 1.5px; background: var(--orange);
  }
  .contact {
    position: absolute; left: 56px; top: 226px;
    list-style: none; color: var(--ink-soft); font-size: 15px; line-height: 28px;
  }
  .contact li { display: flex; align-items: center; gap: 10px; }
  .contact svg { width: 14px; height: 14px; flex: none; }
  .person {
    position: absolute; right: 56px; top: 120px; text-align: right;
  }
  .person-name {
    color: var(--navy); font-weight: 800; font-size: 26px; letter-spacing: 0.02em;
    text-transform: uppercase;
  }
  .person-title {
    color: var(--ink-soft); font-style: italic; font-size: 17px; margin-top: 4px;
  }
</style>
</head>
<body>
<main class="sheet">
  <section class="card card-front" aria-label="Business card front">
    <div class="brand"><span class="brand-dot"></span>CrewCare Clinics</div>
    <div class="person">
      <p class="person-name">Martin Hale</p>
      <p class="person-title">President</p>
    </div>
    <div class="divider"></div>
    <ul class="contact">
      <li>
        <svg viewBox="0 0 16 16" aria-hidden="true"><path fill="#1e9ad6" d="M3.6 1.5l2.3 2.7-1.3 1.8a9 9 0 0 0 5.4 5.4l1.8-1.3 2.7 2.3-1.6 2.1C6.6 14.3 1.7 9.4 1.5 3.1z"/></svg>
        555-014-2290
      </li>
      <li>
        <svg viewBox="0 0 16 16" aria-hidden="true"><rect x="1" y="3" width="14" height="10" rx="1" fill="#1e9ad6"/><path d="M1.5 3.8L8 9l6.5-5.2" stroke="#fff" stroke-width="1.2" fill="none"/></svg>
        martin@crewcareclinics.com
      </li>
      <li>
        <svg viewBox="0 0 16 16" aria-hidden="true"><circle cx="8" cy="8" r="7" fill="#1e9ad6"/><path d="M1 8h14M8 1c-3 3.5-3 10.5 0 14M8 1c3 3.5 3 10.5 0 14" stroke="#fff" stroke-width="1" fill="none"/></svg>
        www.crewcareclinics.com
      </li>
    </ul>
  </section>
  <section class="card card-back" aria-label="Business card back">
    <div class="brand"><span class="brand-dot"></span>CrewCare Clinics</div>
  </section>
</main>
</body>
</html>
```